Webpage for co-working space for tech startups

We have an established co-working space in Aalborg Denmark where we have around 30 companies sharing office space. We are starting a new chapter for us and would like to have a new graphical image - new logo and new webpage, but keep the same name. The webpage should be professional, but also "fun", not too serious. We are all about working hard on our companies, but also taking some time off in between and being social and having fun. We are not corporate, but want to project the image that we are serious about what we do.

We currently have a black/red logo (see www.hivedesk.dk or test.hivedesk.dk), but are interesting in having a new logo design, so colour can be chosen freely. Currently our logo is a big HIVE and a little desk underneath the HIVE. The new logo will be one word "hivedesk" with a small logo before or on top.

If we can make a good webpage for this project, then I have a second more simple project which is also a small single page wordpress site which I would also like to have made.

Target Market(s)

tech startups - relatively new companies, typically younger people 20-35 with a tech background - business or programming, preferably both

Industry/Entity Type

HIVE

Logo Text

hivedesk

Coding

Coded - Design and coding required

Number of Pages Required

4 page

Font styles to use
Sans Serif

Colors

Designer to choose colors to be used in the design.

Requirements
Must have
• Wordpress CMS.
• Mobile and PC optimized
• 2 languages - English and Danish
• Four sections, could be four pages, or four sections of a single page.
• "Home", "Residents", "Our Working Space", "Our Event Space"
• Footer of page or pages should have contact information.
• "Home" has some information about who we are and what we do
• "Residents" has a list of all our residents - it should be possible to easily add and removed new / old residents - See one example here: http://test.hivedesk.dk/en_GB/beboere/ or another example here: http://www.hivedesk.dk/beboere/ - one of our colleagues http://pilotbarn.dk/startups/ or another one of our colleagues http://www.brightkelpyard.dk/residents/
• "Our working space" will have a description of our building, a map of where it is and a bunch of photos which show the different offices, meeting rooms and people working
• "Our events space" will have a description of our event spaces, details of cost + different arrangments of furniture, and lots of photos of events, see here for an example http://www.hivedesk.dk/lej-vores-lokaler/
• Our current webpage - www.hivedesk.dk was put together very quickly and has not really been optimized. We started a new webpage test.hivedesk.dk, but it was never really finished.
• We are looking for a simple webpage, not too much going on. Examples of some of our colleagues in the business http://pilotbarn.dk/, http://www.brightkelpyard.dk/,
Nice to have
• http://www.brightkelpyard.dk/ is a really good template for us. If we can get something like this, we are happy.

```html
<!DOCTYPE html>
<html lang="en">
<head>
<meta charset="utf-8">
<title>HiveDesk – Co-working Space</title>
<link href="https://fonts.googleapis.com/css2?family=Montserrat:wght@500;600;700;800&family=Lato:wght@400;700&display=swap" rel="stylesheet">
<style>
:root{
  --red:#d0080f;
  --red-dark:#b8070d;
  --ink:#111111;
  --text:#444444;
  --white:#ffffff;
  --partner:#3a3a3a;
  --footer:#262626;
  --footer-line:#4a4a4a;
}
*{box-sizing:border-box;margin:0;padding:0}
html,body{width:1200px;height:3930px;overflow:hidden}
body{position:relative;background:var(--white);font-family:'Lato',Arial,sans-serif;color:var(--text)}
.abs{position:absolute}
.head-font{font-family:'Montserrat',Arial,sans-serif}

/* Hero */
.hero{left:0;top:0;width:1200px;height:700px;clip-path:polygon(0 0,100% 0,100% 695px,0 563px);
  background:linear-gradient(180deg,rgba(30,30,34,.30),rgba(30,30,34,.60)),linear-gradient(100deg,#6b6d71 0%,#a7a8ab 35%,#cfcfd1 60%,#7c7e82 100%)}
.brand{display:flex;align-items:center;gap:10px;color:var(--white);font-family:'Montserrat',Arial,sans-serif;font-weight:800;font-size:30px;letter-spacing:1px}
.brand-mark{width:20px;height:20px;background:var(--white)}
.nav{top:62px;left:655px;display:flex;gap:26px;font-size:14px;color:var(--white)}
.nav a{color:inherit;text-decoration:none;padding:4px 6px}
.nav .active{border:2px solid var(--red);background:rgba(208,8,15,.6)}
.lang{top:16px;left:926px;width:56px;height:16px;background:var(--white);border-radius:2px;display:flex;align-items:center;gap:4px;padding:0 4px;font-size:7px;color:#333}
.lang-flag{width:12px;height:8px;background:linear-gradient(180deg,#c22 0 50%,#235 50%)}
.hero-kicker{left:314px;top:242px;color:var(--white);font-weight:700;font-size:30px}
.hero-title{left:305px;top:270px;color:var(--white);font-weight:700;font-size:56px;letter-spacing:1px}
.hero-sub{left:0;width:1200px;top:340px;text-align:center;color:#eee;font-size:13px}
.btn{display:flex;align-items:center;justify-content:center;font-family:'Montserrat',Arial,sans-serif;font-weight:600;font-size:12px;letter-spacing:.5px;text-transform:uppercase;text-decoration:none}
.btn-light{background:var(--white);color:#222}
.btn-red{background:var(--red);color:var(--white)}

/* Section headings */
.section-title{left:0;width:1200px;text-align:center;font-weight:800;font-size:46px;color:var(--ink);letter-spacing:1px;line-height:56px}
.section-title .accent{color:var(--red)}
.rule{height:2px;width:160px;left:520px;background:var(--red)}
.rule-white{background:rgba(255,255,255,.7)}
.body-text{left:290px;width:620px;text-align:center;font-size:12.5px;line-height:1.55;color:var(--text)}
.white{color:var(--white)}

/* Resident */
.resident{left:0;top:1048px;width:1200px;height:610px;clip-path:polygon(0 0,100% 100px,100% 100%,0 460px);
  background:linear-gradient(180deg,#d9070e,var(--red-dark))}

/* Facilities */
.facility{width:200px;text-align:center;font-size:12px;text-transform:uppercase;color:#333}
.facility svg{display:block;margin:0 auto 12px;width:44px;height:38px}

/* Working spaces */
.spaces{left:0;top:2178px;width:1200px;height:500px;clip-path:polygon(0 0,100% 40px,100% 380px,0 494px);
  background:linear-gradient(160deg,#d6131a,#c5090f 60%,#d52027)}
.space-photo{top:2423px;width:202px;height:202px}
.arrow-btn{top:2662px;width:28px;height:28px;display:flex;align-items:center;justify-content:center;border-radius:3px}

/* Events */
.event-photo{left:0;top:2672px;width:720px;height:700px;
  background:linear-gradient(90deg,rgba(255,255,255,0) 0%,rgba(255,255,255,0) 45%,#fff 95%),linear-gradient(180deg,rgba(255,255,255,0) 70%,#fff 100%),linear-gradient(120deg,#6b7a90 0%,#b49a86 35%,#d9d4cf 70%)}
.event{left:498px;display:flex;gap:10px}
.event-date{width:89px;height:58px;background:var(--red);color:var(--white);text-align:center;font-family:'Montserrat',Arial,sans-serif}
.event-date b{display:block;font-size:24px;font-weight:800;line-height:34px}
.event-date span{display:block;font-size:9px;border-top:1px solid rgba(255,255,255,.6);margin:0 8px;padding-top:3px}
.event-name{font-family:'Montserrat',Arial,sans-serif;font-weight:700;color:var(--red);font-size:20px;line-height:22px}
.event-text{font-size:12px;line-height:1.4;color:#333;width:330px}

/* Partners */
.partner{font-family:'Montserrat',Arial,sans-serif;font-weight:600;font-size:14px;letter-spacing:1px;color:var(--partner);text-transform:uppercase}

/* Footer */
.footer{left:0;top:3595px;width:1200px;height:335px;background:var(--footer);clip-path:polygon(0 0,100% 35px,100% 100%,0 100%)}
.foot-col h4{font-family:'Montserrat',Arial,sans-serif;color:var(--white);font-size:14px;letter-spacing:1px;margin-bottom:8px}
.foot-col a{display:block;color:#ddd;font-size:12px;line-height:15px;text-decoration:none}
.subscribe-input{width:128px;height:26px;background:var(--white);color:#888;font-size:11px;padding:6px 8px}
.subscribe-btn{width:32px;height:26px;background:var(--red);display:flex;align-items:center;justify-content:center}
.social-sq{width:18px;height:18px;background:#4a5f8a}
.copyright{left:0;width:1200px;top:3890px;text-align:center;color:#ccc;font-size:11px}
</style>
</head>
<body>

<!-- Hero -->
<div class="abs hero" role="img" aria-label="Photo of a bright co-working room with a long table, black chairs and a potted plant"></div>
<div class="abs brand" style="left:190px;top:55px"><span class="brand-mark"></span>HIVEDESK</div>
<div class="abs lang"><span class="lang-flag"></span>ENGLISH</div>
<nav class="abs nav">
  <a class="active" href="#">Home</a>
  <a href="#">Residents</a>
  <a href="#">Our Working Space</a>
  <a href="#">Our Event Space</a>
</nav>
<div class="abs hero-kicker head-font">HIVE</div>
<h1 class="abs hero-title head-font">CO-WORKING SPACE</h1>
<p class="abs hero-sub">The corporate community at HiveDesk is a community of tech entrepreneurs with global growth ambitions.</p>
<a class="abs btn btn-light" style="left:435px;top:377px;width:157px;height:42px" href="#">Read more</a>
<a class="abs btn btn-red" style="left:610px;top:377px;width:158px;height:42px" href="#">Book a tour</a>

<!-- About -->
<h2 class="abs section-title head-font" style="top:766px">ABOUT <span class="accent">HIVE</span></h2>
<div class="abs rule" style="top:845px"></div>
<p class="abs body-text" style="top:872px">The corporate community at HiveDesk is a community of tech entrepreneurs with global growth ambitions. The vision is to create the best possible conditions for North Jutland entrepreneurs by offering them an environment where they can share knowledge, experience, resources, ideas, motivation and inspiration daily.</p>
<p class="abs body-text" style="top:930px">With its 2,200 m2, HiveDesk can offer both individual offices, flexspaces, meeting rooms, community rooms and smaller prototype workshops. Common to companies is their global ambitions and scalable potential.</p>
<a class="abs btn btn-red" style="left:521px;top:992px;width:157px;height:38px" href="#">Read more</a>

<!-- Resident -->
<div class="abs resident" role="img" aria-label="Red-tinted photo of a wooden house facade with white windows"></div>
<h2 class="abs section-title head-font white" style="top:1201px;font-size:44px">RESIDENT</h2>
<div class="abs rule rule-white" style="top:1268px;width:140px;left:530px"></div>
<div class="abs head-font white" style="left:0;width:1200px;top:1312px;text-align:center;font-weight:700;font-size:17px">KERNEN IN HIVEDESK</div>
<p class="abs body-text white" style="top:1347px;left:270px;width:660px;font-size:12px">At HiveDesk, we do not call the companies at the castle for renters – they are so much more than that. They are inhabitants. These are the ones that help create the right atmosphere. They all form equal in the community. They all have something unique to contribute with and although everyone is doing something widely different, residents have their global ambitions and scalable potential in common.</p>
<p class="abs body-text white" style="top:1424px;font-size:12px">Learn more about what we offer residents.</p>
<a class="abs btn btn-light" style="left:521px;top:1462px;width:157px;height:42px" href="#">Learn more</a>

<!-- Facilities -->
<h2 class="abs section-title head-font" style="top:1660px">WORK SPACE <span class="accent">FACILITIES</span></h2>
<div class="abs rule" style="top:1734px"></div>

<div class="abs facility" style="left:251px;top:1822px">
  <svg viewBox="0 0 44 38" fill="none" stroke="#d0080f" stroke-width="2.4" stroke-linecap="round"><path d="M4 14a26 26 0 0 1 36 0"/><path d="M10 20a17 17 0 0 1 24 0"/><path d="M16 26a8 8 0 0 1 12 0"/><circle cx="22" cy="32" r="1.8" fill="#d0080f"/></svg>
  Highspeed internet</div>
<div class="abs facility" style="left:500px;top:1822px">
  <svg viewBox="0 0 44 38" fill="none" stroke="#d0080f" stroke-width="2.2" stroke-linecap="round"><path d="M9 14h22v10a9 9 0 0 1-9 9h-4a9 9 0 0 1-9-9z"/><path d="M31 17h3a4 4 0 0 1 0 8h-3"/><path d="M17 4c-2 3 2 4 0 7M23 4c-2 3 2 4 0 7"/></svg>
  Free coffe everyday</div>
<div class="abs facility" style="left:744px;top:1822px">
  <svg viewBox="0 0 44 38" fill="none" stroke="#d0080f" stroke-width="2.2" stroke-linecap="round"><path d="M12 10h20c6 0 9 14 8 18s-5 4-8 0l-3-4H15l-3 4c-3 4-7 4-8 0s2-18 8-18z"/><path d="M13 17v6M10 20h6"/><circle cx="29" cy="18" r="1.3"/><circle cx="33" cy="21" r="1.3"/></svg>
  Game station</div>

<div class="abs facility" style="left:251px;top:1982px">
  <svg viewBox="0 0 44 38" fill="none" stroke="#d0080f" stroke-width="2.2" stroke-linejoin="round"><path d="M4 5h22v14H13l-5 5v-5H4z"/><path d="M30 12h10v14h-4v5l-5-5H18v-4"/></svg>
  Meeting room</div>
<div class="abs facility" style="left:500px;top:1982px">
  <svg viewBox="0 0 44 38" fill="none" stroke="#d0080f" stroke-width="2.2" stroke-linecap="round"><path d="M22 2v4"/><rect x="5" y="6" width="34" height="22"/><path d="M16 28l-4 8M28 28l4 8"/></svg>
  Conference room</div>
<div class="abs facility" style="left:744px;top:1982px">
  <svg viewBox="0 0 44 38" fill="none" stroke="#d0080f" stroke-width="2"><rect x="4" y="3" width="36" height="32"/><path d="M4 10h36M13 10v25M22 10v25M31 10v25"/><path d="M8 16v4M17 16v4M26 16v4M35 16v4"/></svg>
  Dedicated lockers</div>

<a class="abs btn btn-red" style="left:506px;top:2128px;width:188px;height:42px" href="#">Explore all facilities</a>

<!-- Event photo (under spaces band) -->
<div class="abs event-photo" role="img" aria-label="Photo of two young men working on laptops at a shared desk"></div>

<!-- Working spaces -->
<div class="abs spaces" role="img" aria-label="Red-tinted photo of an office with tables and chairs"></div>
<h2 class="abs section-title head-font white" style="top:2304px;font-size:44px">OUR WORKNG SPACES</h2>
<div class="abs rule rule-white" style="top:2380px"></div>
<div class="abs space-photo" style="left:288px;background:linear-gradient(160deg,#e7e4df,#a89a86 60%,#6e5a45)" role="img" aria-label="Photo of a lounge with armchairs and a wall screen"></div>
<div class="abs space-photo" style="left:498px;background:linear-gradient(160deg,#5a5e63,#2c2f33 60%,#4b5a48)" role="img" aria-label="Photo of a dark open-plan workspace with desks"></div>
<svg class="abs" style="left:581px;top:2506px" width="36" height="36" viewBox="0 0 36 36" fill="none" stroke="#ffffff" stroke-width="2.4" stroke-linecap="round"><circle cx="15" cy="15" r="10"/><path d="M23 23l9 9M15 10v10M10 15h10"/></svg>
<div class="abs space-photo" style="left:707px;background:linear-gradient(160deg,#f1f3f6,#c3ccd6 55%,#6f85a0)" role="img" aria-label="Photo of a bright meeting room with a long table"></div>
<div class="abs arrow-btn" style="left:563px;background:#ffffff">
  <svg width="12" height="12" viewBox="0 0 12 12" fill="none" stroke="#111" stroke-width="2.4"><path d="M8 1L3 6l5 5"/></svg></div>
<div class="abs arrow-btn" style="left:605px;background:#111111">
  <svg width="12" height="12" viewBox="0 0 12 12" fill="none" stroke="#fff" stroke-width="2.4"><path d="M4 1l5 5-5 5"/></svg></div>

<!-- Events -->
<h2 class="abs head-font" style="left:370px;top:2880px;font-weight:800;font-size:44px;line-height:56px;color:var(--ink);letter-spacing:1px">OUR EVENT <span style="color:var(--red)">SPACES</span></h2>
<div class="abs rule" style="top:2952px"></div>

<div class="abs event" style="top:3002px">
  <div class="event-date"><b>DEC</b><span>1.2018</span></div>
  <div><div class="event-name">EVENT 1</div><p class="event-text">Lorem Ipsum is simply dummy text of the printing and typesetting industry.</p></div>
</div>
<div class="abs event" style="top:3078px">
  <div class="event-date"><b>DEC</b><span>1.2018</span></div>
  <div><div class="event-name">EVENT 1</div><p class="event-text">Lorem Ipsum is simply dummy text of the printing and typesetting industry.</p></div>
</div>
<div class="abs event" style="top:3154px">
  <div class="event-date"><b>DEC</b><span>1.2018</span></div>
  <div><div class="event-name">EVENT 1</div><p class="event-text">Lorem Ipsum is simply dummy text of the printing and typesetting industry.</p></div>
</div>
<a class="abs btn btn-red" style="left:524px;top:3250px;width:160px;height:38px" href="#">Check all events</a>

<!-- Partners -->
<div class="abs partner" style="left:290px;top:3520px">Meridal Group</div>
<div class="abs partner" style="left:470px;top:3545px">Brevik Partners</div>
<div class="abs partner" style="left:664px;top:3563px">Oksen Invest</div>
<div class="abs partner" style="left:808px;top:3575px">Tavlund Studio</div>

<!-- Footer -->
<footer class="abs footer"></footer>
<div class="abs brand" style="left:190px;top:3782px;font-size:28px"><span class="brand-mark" style="width:18px;height:18px"></span>HIVEDESK</div>
<div class="abs foot-col" style="left:414px;top:3762px"><h4>ABOUT</h4><a href="#">About Us</a><a href="#">Contact Us</a><a href="#">F.A.Q</a><a href="#">Privacy</a></div>
<div class="abs foot-col" style="left:558px;top:3762px"><h4>SPACE</h4><a href="#">Resident</a><a href="#">Working Spaces</a><a href="#">Event Spaces</a></div>
<div class="abs foot-col" style="left:713px;top:3762px"><h4>LEGAL</h4><a href="#">Privacy</a><a href="#">Terms</a><a href="#">Advertise</a><a href="#">Sponsors</a></div>
<div class="abs foot-col" style="left:849px;top:3762px"><h4>SUBSCRIBE</h4></div>
<div class="abs" style="left:849px;top:3788px;display:flex">
  <div class="subscribe-input">E-Mail Address</div>
  <div class="subscribe-btn"><svg width="14" height="14" viewBox="0 0 14 14" fill="#fff"><path d="M1 6.5L13 1 10 13 7 9 1 6.5z"/></svg></div>
</div>
<div class="abs" style="left:849px;top:3826px;display:flex;align-items:center;gap:14px">
  <span class="head-font" style="color:#fff;font-weight:700;font-size:14px;letter-spacing:1px">FOLLOW US</span>
  <span class="social-sq"></span>
</div>
<div class="abs" style="left:190px;top:3870px;width:820px;height:1px;background:var(--footer-line)"></div>
<p class="abs copyright">© Copyright 2018 . hivedesk.All Right Reserved</p>

</body>
</html>
```